Solar Carport

Copperfen renewables is looking for a flyer promoting our solar carport design in Alberta, BC and Saskatchewan. We call it the Lanternway. We have specific color pallet. Should be flashy, endorse local manufacturing, and the over all design should have a green feel to it. We would also like to add this to our website. We will offer this design in steel and wood beam frame.

```html
<!DOCTYPE html>
<html lang="en">
<head>
<meta charset="utf-8">
<title>Copperfen renewables – Solar Flyer</title>
<link rel="stylesheet" href="https://fonts.googleapis.com/css2?family=Archivo+Black&family=Arimo:wght@400;700&display=swap">
<style>
  :root{
    --page-bg:#d9d9d9;
    --green:#3f9a40;
    --green-deep:#2f8a35;
    --ring-green:#6cc04a;
    --ring-blue:#4fb8e6;
    --band:#e2eb9b;
    --ink:#1b1b1b;
    --white:#ffffff;
    --strip-dark:#1e1e1e;
    --logo-dark:#1c1d22;
  }
  *{margin:0;padding:0;box-sizing:border-box}
  html,body{width:1200px;height:1000px;overflow:hidden;background:var(--page-bg)}
  .flyer{
    position:absolute;left:261px;top:20px;width:677px;height:960px;
    background:linear-gradient(180deg,#2f7d6a 0,#3a8f55 280px,var(--green) 330px,var(--green-deep) 890px);
    overflow:hidden;font-family:"Arimo",Arial,sans-serif;
  }
  .hero-scene{
    position:absolute;left:0;top:0;width:677px;height:310px;
    background:
      linear-gradient(90deg,rgba(20,50,20,.45) 0,rgba(20,50,20,0) 35%,rgba(200,220,170,.25) 50%,rgba(20,50,20,0) 65%,rgba(20,50,20,.35) 100%),
      linear-gradient(180deg,#c7dde4 0,#9fb58a 18px,#5f7f3c 50px,#35562a 110px,#2f4e25 148px,#9fae7a 153px,#5f7a45 158px,#4b6a3a 190px,#3f7a5c 230px,#3a8f6a 262px,rgba(63,154,64,0) 310px);
  }
  .logo-badge{
    position:absolute;left:270px;top:8px;width:140px;height:140px;border-radius:50%;
    background:var(--logo-dark);display:flex;align-items:center;justify-content:center;text-align:center;
  }
  .logo-name{font-family:"Arimo",Arial,sans-serif;font-weight:700;font-size:17px;line-height:1.2;color:var(--white);}
  .headline{
    position:absolute;left:0;top:172px;width:677px;text-align:center;
    font-family:"Archivo Black",Arial,sans-serif;font-size:27px;line-height:37px;color:var(--white);letter-spacing:.6px;
  }
  .band{
    position:absolute;left:84px;width:520px;height:29px;
    background:linear-gradient(90deg,rgba(226,235,155,0) 0,var(--band) 12%,var(--band) 88%,rgba(226,235,155,0) 100%);
    display:flex;align-items:center;justify-content:center;font-size:20.5px;color:var(--ink);
  }
  .band-specialists{top:270px}
  .band-different{top:543px}
  .artwork{position:absolute;left:0;top:0;width:677px;height:960px}
  .tag{
    position:absolute;top:581px;width:137px;height:25px;background:var(--band);
    display:flex;align-items:center;justify-content:center;font-size:21.5px;color:var(--ink);
  }
  .tag-assets{left:114px}
  .tag-products{left:431px}
  .tag-line{position:absolute;top:609px;font-size:22px;color:var(--white);white-space:nowrap;text-align:center;}
  .tag-line-assets{left:43px;width:280px}
  .tag-line-products{left:340px;width:325px}
  .web-strip{
    position:absolute;left:0;top:891px;width:677px;height:26px;background:var(--strip-dark);
    color:var(--white);font-size:18px;display:flex;align-items:center;justify-content:center;
  }
  .contact-strip{
    position:absolute;left:0;top:917px;width:677px;height:43px;background:var(--white);
    color:var(--ink);font-size:17.5px;
  }
  .contact-item{display:flex;align-items:center;gap:14px;position:absolute;top:9px}
  .contact-phone{left:37px}
  .contact-mail{left:338px}
  .icon{width:24px;height:24px}
</style>
</head>
<body>
<main class="flyer">
  <div class="hero-scene" role="img" aria-label="Photo of a forested mountain lake reflecting the hills"></div>

  <div class="logo-badge"><span class="logo-name">Copperfen<br>renewables</span></div>

  <h1 class="headline">WHAT IS HOLDING YOU BACK<br>FROM GOING SOLAR?</h1>

  <div class="band band-specialists">YOUR RENEWABLE ENERGY SPECIALISTS</div>

  <svg class="artwork" viewBox="0 0 677 960">
    <defs>
      <linearGradient id="tone-rooftop" x1="0" y1="0" x2="0" y2="1">
        <stop offset="0" stop-color="#7c8088"/>
        <stop offset=".2" stop-color="#2c3248"/>
        <stop offset=".65" stop-color="#242a3e"/>
        <stop offset=".78" stop-color="#6d7078"/>
        <stop offset=".9" stop-color="#d8dadc"/>
        <stop offset="1" stop-color="#3a3c40"/>
      </linearGradient>
      <linearGradient id="tone-rv" x1="0" y1="0" x2="0" y2="1">
        <stop offset="0" stop-color="#5f9a3c"/>
        <stop offset=".25" stop-color="#8eb066"/>
        <stop offset=".4" stop-color="#dfe1e0"/>
        <stop offset=".55" stop-color="#2b3350"/>
        <stop offset=".85" stop-color="#263050"/>
        <stop offset="1" stop-color="#e4e6e6"/>
      </linearGradient>
      <linearGradient id="tone-ground" x1="0" y1="0" x2="0" y2="1">
        <stop offset="0" stop-color="#c9cbcc"/>
        <stop offset=".3" stop-color="#7d7a74"/>
        <stop offset=".42" stop-color="#39405a"/>
        <stop offset=".65" stop-color="#2e3552"/>
        <stop offset=".75" stop-color="#e9ecee"/>
        <stop offset="1" stop-color="#f4f5f6"/>
      </linearGradient>
      <linearGradient id="tone-wood-side" x1="0" y1="0" x2="0" y2="1">
        <stop offset="0" stop-color="#7c9ab8"/>
        <stop offset=".25" stop-color="#a8b8c6"/>
        <stop offset=".33" stop-color="#d98a3a"/>
        <stop offset=".55" stop-color="#c9782e"/>
        <stop offset=".6" stop-color="#6a6a6a"/>
        <stop offset=".75" stop-color="#2b2b2b"/>
        <stop offset="1" stop-color="#111"/>
      </linearGradient>
      <linearGradient id="tone-steel" x1="0" y1="0" x2="0" y2="1">
        <stop offset="0" stop-color="#6a6c6e"/>
        <stop offset=".22" stop-color="#5a5c60"/>
        <stop offset=".3" stop-color="#2a3048"/>
        <stop offset=".55" stop-color="#343a52"/>
        <stop offset=".6" stop-color="#d8d8d8"/>
        <stop offset=".65" stop-color="#3c3c3c"/>
        <stop offset="1" stop-color="#141414"/>
      </linearGradient>
      <linearGradient id="tone-wood-front" x1="0" y1="0" x2="0" y2="1">
        <stop offset="0" stop-color="#7f9ec0"/>
        <stop offset=".28" stop-color="#9fb3c6"/>
        <stop offset=".33" stop-color="#d4803a"/>
        <stop offset=".5" stop-color="#c0702c"/>
        <stop offset=".55" stop-color="#6b6b6b"/>
        <stop offset=".8" stop-color="#2a2a2a"/>
        <stop offset="1" stop-color="#121212"/>
      </linearGradient>
    </defs>
    <g fill="none" stroke="var(--ring-blue)" stroke-width="4">
      <path d="M18 425 A103 103 0 0 0 222 425"/>
      <path d="M236 416 A103 103 0 0 1 442 416"/>
      <path d="M450 425 A103 103 0 0 0 656 425"/>
      <path d="M21 752 A103 103 0 0 1 227 752"/>
      <path d="M234 766 A103 103 0 0 0 440 766"/>
      <path d="M452 752 A103 103 0 0 1 658 752"/>
    </g>
    <g fill="var(--ring-green)">
      <circle cx="120" cy="417" r="94"/>
      <circle cx="339" cy="425" r="94"/>
      <circle cx="553" cy="417" r="94"/>
      <circle cx="124" cy="759" r="94"/>
      <circle cx="337" cy="766" r="94"/>
      <circle cx="555" cy="759" r="94"/>
    </g>
    <circle cx="120" cy="417" r="84" fill="url(#tone-rooftop)" role="img" aria-label="Photo of rooftop solar panels on a house"/>
    <circle cx="339" cy="425" r="84" fill="url(#tone-rv)" role="img" aria-label="Photo of solar panels on an RV roof"/>
    <circle cx="553" cy="417" r="84" fill="url(#tone-ground)" role="img" aria-label="Photo of a ground-mount solar array in snow"/>
    <circle cx="124" cy="759" r="84" fill="url(#tone-wood-side)" role="img" aria-label="Rendering of the Lanternway wood beam solar carport"/>
    <circle cx="337" cy="766" r="84" fill="url(#tone-steel)" role="img" aria-label="Rendering of the Lanternway steel frame solar carport"/>
    <circle cx="555" cy="759" r="84" fill="url(#tone-wood-front)" role="img" aria-label="Rendering of the Lanternway wood beam solar carport from the front"/>
  </svg>

  <div class="band band-different">WHAT MAKES US DIFFERENT</div>

  <div class="tag tag-assets">Our Assets</div>
  <div class="tag tag-products">Products</div>
  <p class="tag-line tag-line-assets">We have the total package</p>
  <p class="tag-line tag-line-products">We work with all manufacturers</p>

  <div class="web-strip">For more informations visit our website : https://copperfenrenewables.com/</div>
  <div class="contact-strip">
    <div class="contact-item contact-phone">
      <svg class="icon" viewBox="0 0 24 24"><circle cx="12" cy="12" r="12" fill="var(--ring-green)"/><path d="M8.2 6.5c.5-.4 1.1-.3 1.4.2l1 1.7c.3.5.2 1-.2 1.3l-.7.6c.6 1.4 1.6 2.5 3 3.1l.6-.7c.4-.4.9-.5 1.3-.2l1.7 1c.5.3.6 1 .2 1.4l-.8.9c-.6.6-1.6.8-2.4.4-2.8-1.3-4.9-3.4-6-6.2-.3-.8-.1-1.7.5-2.3z" fill="var(--white)"/></svg>
      <span>403.555.0182 / 780.555.0147</span>
    </div>
    <div class="contact-item contact-mail">
      <svg class="icon" viewBox="0 0 24 24"><circle cx="12" cy="12" r="12" fill="var(--ring-green)"/><g fill="none" stroke="var(--white)" stroke-width="1.3"><circle cx="12" cy="12" r="7"/><ellipse cx="12" cy="12" rx="3" ry="7"/><path d="M5 12h14M6 8.5h12M6 15.5h12"/></g></svg>
      <span>sales@copperfenrenewables.com</span>
    </div>
  </div>
</main>
</body>
</html>
```